Detail Shop Business card design

i need a business card design for my new detailing company called 'Brisk's Polish Works'. i want an all black and white design . simple, direct and to the point. i want the designer to choose a fitting font to match the logothe front should have logo, address, phone and email and the back side should have a slogan and text indicating that we offer services on anything including cars, trucks, motorcycles and RVs. slogan will read "we take pride in your ride"
maybe also very small on the back side the IG icon with Brisks_Polish_Works

phone 208.417.6352
address 3847 E Larkin Ave
Spokane WA 99214
email: BrisksPolish@mailvexo.com

Target Market(s)

all ages , auto enthusiasts

Industry/Entity Type

Automotive

Contact Information for Business Card

the front should have logo, address, phone and email and the back side should have a slogan and text indicating that we offer services on anything including cars, trucks, motorcycles and RVs. slogan will read "we take pride in your ride"

phone 208.417.6352
address 3847 E Larkin Ave
Spokane WA 99214

Colors
000000
ffffff

Requirements
Must have
• bold font and very simple design with good spacing
Nice to have
• anything creative from the designer indicating we service any types of vehicles
Should not have
• any colors ,

```html
<!DOCTYPE html>
<html lang="en">
<head>
<meta charset="utf-8">
<title>Brisk's Polish Works – Business Card</title>
<link href="https://fonts.googleapis.com/css2?family=Roboto:wght@400;500;700&family=Pathway+Gothic+One&display=swap" rel="stylesheet">
<style>
  :root {
    --ink: #000000;
    --paper: #ffffff;
    --text-grey: #3a3a3a;
    --backdrop: #e4e4e4;
    --art-light: #d6d6d6;
    --art-dark: #7a7a7a;
  }
  html, body { margin: 0; padding: 0; overflow: hidden; }
  body {
    width: 1200px; height: 960px; position: relative;
    background: var(--backdrop);
    font-family: "Roboto", Arial, sans-serif;
  }
  .card {
    position: absolute; width: 600px; height: 343px;
    background: var(--paper); overflow: hidden;
    box-shadow: 0 3px 8px rgba(0,0,0,.25);
  }
  .card--front { left: 314px; top: 113px; }
  .card--back { left: 311px; top: 472px; }

  .brand {
    position: absolute; left: 36px; top: 40px; width: 160px;
    display: flex; flex-direction: column; align-items: center; gap: 10px;
  }
  .brand__dot { width: 56px; height: 56px; border-radius: 50%; background: var(--ink); }
  .brand__name {
    font-weight: 700; font-size: 18px; line-height: 1.15; color: var(--ink);
    text-align: center; text-transform: uppercase;
  }

  .contact { position: absolute; left: 34px; top: 199px; margin: 0; padding: 0; list-style: none; }
  .contact__item {
    display: flex; align-items: flex-start; gap: 8px;
    font-size: 14px; line-height: 19px; color: var(--text-grey);
  }
  .contact__item--gap { margin-top: 10px; }
  .contact__icon { width: 14px; height: 14px; margin-top: 3px; flex: none; fill: var(--ink); }

  .nametag { position: absolute; left: 360px; top: 227px; width: 240px; height: 70px; }
  .nametag__band {
    position: absolute; left: 60px; top: 5px; width: 180px; height: 60px; background: var(--ink);
    color: var(--paper); text-align: right; box-sizing: border-box; padding: 8px 20px 0 0;
  }
  .nametag__name { font-size: 20px; font-weight: 500; line-height: 24px; text-transform: uppercase; }
  .nametag__title { font-size: 14px; font-weight: 500; line-height: 18px; text-transform: uppercase; }
  .nametag__badge { position: absolute; left: 0; top: 0; width: 70px; height: 70px; }

  .services {
    position: absolute; top: 48px; left: 0; width: 100%; text-align: center;
    font-family: "Pathway Gothic One", "Arial Narrow", sans-serif; font-size: 21px; color: var(--ink);
  }
  .vehicle-art {
    position: absolute; left: 18px; top: 108px; width: 554px; height: 196px;
    background: linear-gradient(180deg, var(--art-light), var(--art-dark));
    border-radius: 60px 40px 20px 20px;
  }
  .ground { position: absolute; left: 0; bottom: 0; width: 600px; height: 56px; }
  .slogan {
    position: absolute; left: 0; bottom: 18px; width: 100%; text-align: center;
    color: var(--paper); font-weight: 700; font-size: 16px; letter-spacing: .3px;
  }
</style>
</head>
<body>

<section class="card card--front" aria-label="Card front">
  <div class="brand">
    <span class="brand__dot"></span>
    <span class="brand__name">Brisk's Polish Works</span>
  </div>

  <ul class="contact">
    <li class="contact__item">
      <svg class="contact__icon" viewBox="0 0 14 14"><path d="M7 0a5 5 0 0 0-5 5c0 3.5 5 9 5 9s5-5.5 5-9a5 5 0 0 0-5-5zm0 7a2 2 0 1 1 0-4 2 2 0 0 1 0 4z"/></svg>
      <span>3847 E Larkin Ave<br>Spokane WA 99214</span>
    </li>
    <li class="contact__item contact__item--gap">
      <svg class="contact__icon" viewBox="0 0 14 14"><path d="M3 0l3 3-2 2c1 2 3 4 5 5l2-2 3 3-2 3C6 14 0 8 0 3z"/></svg>
      <span>208.417.6352</span>
    </li>
    <li class="contact__item">
      <svg class="contact__icon" viewBox="0 0 14 14"><path d="M3 0h8v14H3zM4.5 1.5v9h5v-9zM6 12h2v1H6z"/></svg>
      <span>208 593 7140</span>
    </li>
    <li class="contact__item">
      <svg class="contact__icon" viewBox="0 0 14 14"><path d="M0 3h14v1L7 8 0 4zM0 5.5l7 4 7-4V12H0z"/></svg>
      <span>BrisksPolish@mailvexo.com</span>
    </li>
    <li class="contact__item">
      <svg class="contact__icon" viewBox="0 0 14 14"><circle cx="7" cy="7" r="6.5"/><path d="M1 7h12M7 .5v13" stroke="#fff" stroke-width="1"/></svg>
      <span>www.briskspolish.com</span>
    </li>
  </ul>

  <div class="nametag">
    <div class="nametag__band">
      <div class="nametag__name">Dale Mercer</div>
      <div class="nametag__title">CEO/Founder</div>
    </div>
    <svg class="nametag__badge" viewBox="0 0 70 70">
      <circle cx="35" cy="35" r="35" fill="#fff"/>
      <circle cx="35" cy="35" r="33" fill="#000"/>
      <polygon fill="#fff" points="35,9 41.5,27 60,27 45,38.5 50.5,57 35,46 19.5,57 25,38.5 10,27 28.5,27"/>
    </svg>
  </div>
</section>

<section class="card card--back" aria-label="Card back">
  <p class="services" style="margin:0">we offer services on anything including cars, trucks, motorcycles &amp; RVs</p>
  <div class="vehicle-art" role="img" aria-label="Black and white illustration of a hot rod car in side view"></div>
  <svg class="ground" viewBox="0 0 600 56" preserveAspectRatio="none">
    <path d="M0 30 Q120 4 300 4 Q480 4 600 30 V56 H0Z" fill="#000"/>
  </svg>
  <div class="slogan">WE TAKE PRIDE IN YOUR RIDE</div>
</section>

</body>
</html>
```